Accounting firm needing business card / letterhead designed
Marcus L. Trenholm, CPA
marcus@veltrowledger.com
www.veltrowledger.com
842 E Alder Ave Harlow Glen, WI 43827
419-562-0974

```html
<!DOCTYPE html>
<html lang="en">
<head>
<meta charset="utf-8">
<title>Veltrow Ledger – Stationery</title>
<link rel="stylesheet" href="https://fonts.googleapis.com/css2?family=Montserrat:wght@500;600;700;800&family=Arimo:wght@400;700&display=swap">
<style>
  :root {
    --navy: #2b2a72;
    --green: #7cc242;
    --paper: #ffffff;
    --ink: #3a3a3a;
    --stage: #ececec;
    --muted: #c9c9e6;
  }
  * { box-sizing: border-box; margin: 0; padding: 0; }
  html, body { width: 1200px; height: 795px; overflow: hidden; }
  body { background: var(--stage); font-family: "Arimo", Arial, sans-serif; position: relative; }

  /* Letterhead */
  .letterhead {
    position: absolute; left: 90px; top: 60px; width: 470px; height: 665px;
    background: var(--paper); box-shadow: 0 2px 8px rgba(0,0,0,.12);
  }
  .letterhead__contact {
    position: absolute; right: 0; top: 22px; width: 190px; padding: 8px 12px 8px 10px;
    background: var(--navy); border-left: 3px solid var(--green); border-bottom: 3px solid var(--green);
    color: #fff; font-size: 8.5px; line-height: 1.55; text-align: right;
  }
  .letterhead__contact .company span { color: var(--green); }
  .contact-line { display: flex; justify-content: flex-end; align-items: center; gap: 5px; }
  .dot { width: 8px; height: 8px; border-radius: 50%; background: var(--green); flex: none; }
  .letterhead__brand {
    position: absolute; left: 40px; top: 115px;
    font-family: "Montserrat", sans-serif; font-weight: 800; font-size: 32px; color: var(--navy);
    letter-spacing: .5px; line-height: 1;
  }
  .letter {
    position: absolute; left: 40px; right: 40px; top: 230px;
    font-size: 9px; line-height: 1.45; color: var(--ink); text-align: justify;
  }
  .letter__salutation { font-weight: 700; font-size: 10px; margin-bottom: 12px; }
  .letter p + p { margin-top: 10px; }
  .letter__signature {
    display: block; width: 90px; height: 28px; margin-top: 22px;
    background: linear-gradient(90deg, rgba(40,40,40,.12), rgba(40,40,40,.04));
  }
  .letterhead__footer { position: absolute; left: 0; right: 0; bottom: 0; height: 10px; display: flex; align-items: flex-end; }
  .letterhead__footer .band-navy { flex: 7; height: 7px; background: var(--navy); }
  .letterhead__footer .band-green { flex: 3; height: 10px; background: var(--green); }

  /* Business cards */
  .card {
    position: absolute; width: 380px; height: 216px; box-shadow: 0 2px 8px rgba(0,0,0,.14);
    overflow: hidden;
  }
  .card--back { left: 700px; top: 130px; background: var(--navy); }
  .card__map {
    position: absolute; inset: 20px 40px 30px 30px; border-radius: 40%;
    background: radial-gradient(ellipse at center, rgba(255,255,255,.07), rgba(255,255,255,0) 70%);
  }
  .card__brand-center {
    position: absolute; left: 0; right: 0; top: 80px; text-align: center;
    font-family: "Montserrat", sans-serif; font-weight: 800; font-size: 34px; color: #fff; letter-spacing: .5px;
  }
  .card__web {
    position: absolute; right: 60px; top: 140px; width: 150px; border-top: 1px solid var(--muted);
    padding-top: 4px; font-size: 8px; color: var(--muted); text-align: right;
  }

  .card--front { left: 640px; top: 450px; background: var(--paper); display: flex; }
  .card__logo-side { width: 46%; display: flex; align-items: center; justify-content: center; }
  .card__brand {
    font-family: "Montserrat", sans-serif; font-weight: 800; font-size: 24px; color: var(--navy); line-height: 1.05;
  }
  .card__info {
    width: 54%; background: var(--navy); border-left: 4px solid var(--green);
    padding: 24px 16px; color: #fff; font-size: 9px; line-height: 1.6;
  }
  .card__name { font-family: "Montserrat", sans-serif; font-weight: 700; font-size: 12px; color: var(--green); }
  .card__title { margin-bottom: 4px; }
  .card__info .contact-line { justify-content: flex-start; }
</style>
</head>
<body>

<section class="letterhead" aria-label="Letterhead">
  <div class="letterhead__contact">
    <div class="company">Veltrow <span>Ledger</span></div>
    <div>842 E Alder Ave Harlow Glen, WI 43827</div>
    <div class="contact-line">419-562-0974 <i class="dot"></i></div>
    <div class="contact-line">marcus@veltrowledger.com <i class="dot"></i></div>
    <div class="contact-line">www.veltrowledger.com <i class="dot"></i></div>
  </div>

  <div class="letterhead__brand">Veltrow Ledger</div>

  <div class="letter">
    <p class="letter__salutation">Dear Mr. Hale,</p>
    <p>Lorem Ipsum is simply dummy text of the printing and typesetting industry. Lorem Ipsum has been the industry's standard dummy text ever since the 1500s, when an unknown printer took a galley of type and scrambled it to make a type specimen book. It has survived not only five centuries, but also the leap into electronic typesetting, remaining essentially unchanged.</p>
    <p>The standard chunk of Lorem Ipsum used since the 1500s is reproduced below for those interested. Sections 1.10.32 and 1.10.33 from "On Ledgers and Limits" by T. Morrell are also reproduced in their exact original form, accompanied by English versions from the 1914 translation by H. Pellam.</p>
    <p>Lorem Ipsum is simply dummy text of the printing and typesetting industry. Lorem Ipsum has been the industry's standard dummy text ever since the 1500s, when an unknown printer took a galley of type and scrambled it to make a type specimen book. It has survived not only five centuries, but also the leap into electronic typesetting, remaining essentially unchanged. It was popularised in the</p>
    <span class="letter__signature" role="img" aria-label="Handwritten signature"></span>
  </div>

  <div class="letterhead__footer">
    <div class="band-navy"></div>
    <div class="band-green"></div>
  </div>
</section>

<section class="card card--back" aria-label="Business card back">
  <div class="card__map" role="img" aria-label="Faint world map background"></div>
  <div class="card__brand-center">Veltrow Ledger</div>
  <div class="card__web">www.veltrowledger.com</div>
</section>

<section class="card card--front" aria-label="Business card front">
  <div class="card__logo-side">
    <div class="card__brand">Veltrow<br>Ledger</div>
  </div>
  <div class="card__info">
    <div class="card__name">Marcus L. Trenholm</div>
    <div class="card__title">CPA</div>
    <div>Veltrow Ledger</div>
    <div>842 E Alder Ave Harlow Glen, WI 43827</div>
    <div class="contact-line"><i class="dot"></i> 419-562-0974</div>
    <div class="contact-line"><i class="dot"></i> marcus@veltrowledger.com</div>
    <div class="contact-line"><i class="dot"></i> www.veltrowledger.com</div>
  </div>
</section>

</body>
</html>
```